Brookvale Building Company - advertisement poster

I am looking to print some canvas signs to advertise my general contracting company, Brookvale Building Company. The sign will measure 6' long x 3' high so the size should match that ratio. I already have a logo icon, which is the Letter 'B' and some trees that I would like to incorporate, see attached. I would also like the to have the following information listed:
1) phone number: 831-555-0172
2) email: brookvalebuildingcompany@mailnest.example
3) website: brookvalebuildingcompany.example
4) Lic#4826130
5) I want to use this text: "BUILD WITH THE B-CREW!"

The ad should be relatively simple and clean. Black and Green are my company colors. I am open to creative ideas!

Target Market(s)

People looking to renovate their homes

Industry/Entity Type

Construction

Colors
59FF00
82FF00
B8FF75
E3FFCB
F4FFEA

Requirements
Must have
• Must have my company logo
Should not have
• No photos or complex graphics

```html
<!DOCTYPE html>
<html lang="en">
<head>
<meta charset="utf-8">
<title>Brookvale Building Company – Sign</title>
<link rel="stylesheet" href="https://fonts.googleapis.com/css2?family=Archivo+Black&family=Montserrat:wght@500;600;700;800&display=swap">
<style>
  :root {
    --ink: #1f1f1f;
    --green: #6cbf45;
    --white: #ffffff;
    --backdrop: #e4e6e3;
  }
  * { box-sizing: border-box; margin: 0; padding: 0; }
  html, body {
    width: 1200px; height: 800px; overflow: hidden;
    background: var(--backdrop);
  }
  .sign {
    position: absolute; left: 0; top: 100px;
    width: 1200px; height: 600px;
    background: var(--ink);
    font-family: "Montserrat", sans-serif;
    color: var(--white);
  }
  .sign__top { position: absolute; left: 0; top: 0; width: 100%; height: 222px; }
  .brand {
    position: absolute; left: 92px; top: 72px;
    display: flex; align-items: center; gap: 14px;
  }
  .brand__mark { width: 34px; height: 34px; background: var(--green); }
  .brand__name {
    font-weight: 700; font-size: 25px; line-height: 1.15;
    letter-spacing: 1.5px; text-transform: uppercase; color: var(--white);
  }
  .license {
    position: absolute; left: 140px; top: 142px;
    font-weight: 600; font-size: 18px; letter-spacing: 2px;
    color: var(--green);
  }
  .phone {
    position: absolute; right: 58px; top: 62px;
    display: flex; align-items: center; gap: 30px;
  }
  .phone__icon { width: 62px; height: 62px; }
  .phone__number {
    font-weight: 800; font-size: 92px; letter-spacing: 1px; line-height: 1;
  }
  .sign__band {
    position: absolute; left: 0; top: 222px; width: 100%; height: 222px;
    background: var(--green); color: var(--ink); text-align: center;
  }
  .headline__lead {
    position: absolute; left: 0; right: 0; top: 28px;
    font-family: "Archivo Black", sans-serif; font-size: 58px; line-height: 1;
    letter-spacing: 1px; padding-left: 130px;
  }
  .headline__main {
    position: absolute; left: 0; right: 0; top: 88px;
    font-family: "Montserrat", sans-serif; font-weight: 800;
    font-size: 122px; line-height: 1; letter-spacing: 26px;
    padding-left: 60px;
  }
  .sign__contact { position: absolute; left: 0; top: 444px; width: 100%; height: 156px; }
  .contact { position: absolute; top: 30px; display: flex; gap: 16px; }
  .contact--web { left: 92px; }
  .contact--mail { left: 724px; }
  .contact__icon { width: 36px; height: 36px; margin-top: 2px; }
  .contact__name { font-weight: 600; font-size: 31px; letter-spacing: 0.5px; line-height: 1.2; }
  .contact--mail .contact__name { font-size: 26px; }
  .contact__tag {
    display: inline-block; margin-top: 8px;
    background: var(--green); color: var(--ink);
    font-weight: 600; font-size: 22px; padding: 2px 16px; border-radius: 3px;
  }
</style>
</head>
<body>
<main class="sign">
  <header class="sign__top">
    <div class="brand">
      <span class="brand__mark"></span>
      <span class="brand__name">Brookvale<br>Building Company</span>
    </div>
    <p class="license">Lic#4826130</p>
    <div class="phone">
      <svg class="phone__icon" viewBox="0 0 64 64" aria-hidden="true">
        <path d="M14 10c3-2 6-1 7 2l4 9c1 2 0 4-2 5l-4 3c3 7 8 12 15 15l3-4c1-2 3-3 5-2l9 4c3 1 4 4 2 7l-3 4c-3 3-8 4-13 2C25 50 14 39 9 25c-2-5-1-10 2-13z" fill="var(--green)"/>
        <path d="M38 6a20 20 0 0 1 20 20M38 15a11 11 0 0 1 11 11" fill="none" stroke="var(--green)" stroke-width="4" stroke-linecap="round"/>
      </svg>
      <span class="phone__number">831.555.0172</span>
    </div>
  </header>

  <section class="sign__band">
    <h1 class="headline">
      <span class="headline__lead">BUILD WITH THE</span>
      <span class="headline__main">B-CREW!</span>
    </h1>
  </section>

  <footer class="sign__contact">
    <div class="contact contact--web">
      <svg class="contact__icon" viewBox="0 0 40 40" aria-hidden="true">
        <g fill="none" stroke="var(--green)" stroke-width="3">
          <circle cx="20" cy="20" r="16"/>
          <ellipse cx="20" cy="20" rx="7" ry="16"/>
          <path d="M4 20h32M7 11h26M7 29h26"/>
        </g>
      </svg>
      <div>
        <div class="contact__name">BrookvaleBuildingCompany</div>
        <span class="contact__tag">.example</span>
      </div>
    </div>
    <div class="contact contact--mail">
      <svg class="contact__icon" viewBox="0 0 40 40" aria-hidden="true">
        <rect x="3" y="9" width="34" height="22" fill="var(--green)"/>
        <path d="M4 10l16 12 16-12M4 30l12-10M36 30L24 20" fill="none" stroke="var(--ink)" stroke-width="2.5"/>
      </svg>
      <div>
        <div class="contact__name">BrookvaleBuildingCompany</div>
        <span class="contact__tag">@mailnest.example</span>
      </div>
    </div>
  </footer>
</main>
</body>
</html>
```